Fresh Dwelling Tract Guide needs a new Landing Page

I like to get a landing page or website with 2-3 pages to help target home buyers who are looking to buy homes from builders such as TW Residences, Morvik, P.L. Fennick, etc. The landing page/website to be non-cluttered and be able to explain to home buyers that there are many benefits to include me as their buyer's agent when they buy a brand new home from any builders.
I may want to incorporate a short explanation video (animated) on the landing page and then for the viewer to click on a button that will take them to another page where they can search for new homes from different builders.
Target Market(s)
Home buyers looking to buy brand new home from builders such as TW Residences, Morvik, P.L. Fennick, etc.
Industry/Entity Type
Real Estate
Number of Pages Required
2 page
Font styles to use
Requirements
Must have
- The landing page may have the explanation video at the bottom of the landing page (scrolled down) or there may be a CALL TO ACTION button that takes the viewer to the 2nd page to watch the explanation video. Once they watched the explanation video and are still interested, they can click on another CALL TO ACTION button that will take them to another website that they will be able to search for all the available new homes and register their contact information.
Should not have
- No clutters and no dark colors.

```html
<!DOCTYPE html>
<html lang="en">
<head>
<meta charset="utf-8">
<title>Fresh Dwelling Tract Guide — Search for New Homes</title>
<link rel="stylesheet" href="https://fonts.googleapis.com/css2?family=Oswald:wght@400;500&family=Open+Sans:wght@400&family=Roboto:wght@500&display=swap">
<style>
  :root {
    --white: #ffffff;
    --sky-top: #7b9bbb;
    --sky-mid: #93adc6;
    --city-tone: #6a86a4;
    --city-base: #5f7b99;
    --dusk-glow: #e2b48a;
    --accent: #3ad8ae;
    --button-fill: #24a085;
    --button-edge: #1c8a72;
    --footer-bg: rgba(72, 98, 128, 0.78);
    --footer-line: rgba(255, 255, 255, 0.6);
    --text-shadow: rgba(30, 48, 70, 0.55);
    --phone-glyph: #5f7b99;
  }
  * { margin: 0; padding: 0; box-sizing: border-box; }
  html, body { width: 1200px; height: 724px; overflow: hidden; }
  body { position: relative; font-family: "Open Sans", sans-serif; color: var(--white); background: var(--city-base); }

  .hero-photo {
    position: absolute; inset: 0;
    background:
      radial-gradient(ellipse 55% 28% at 8% 88%, var(--dusk-glow) 0%, transparent 70%),
      radial-gradient(ellipse 50% 55% at 58% 72%, var(--city-tone) 0%, transparent 72%),
      linear-gradient(180deg, var(--sky-top) 0%, var(--sky-mid) 42%, var(--city-tone) 72%, var(--city-base) 100%);
  }
  .hero-shade { position: absolute; inset: 0; background: rgba(40, 62, 88, 0.18); }

  .site-header { position: absolute; top: 0; left: 0; width: 100%; height: 124px; }
  .menu-toggle { position: absolute; left: 93px; top: 50px; width: 26px; height: 22px; }
  .menu-toggle span { display: block; height: 4px; background: var(--white); margin-bottom: 5px; border-radius: 1px; }
  .brand-name {
    position: absolute; left: 0; right: 0; top: 44px; text-align: center;
    font-family: "Oswald", sans-serif; font-weight: 500; font-size: 27px; letter-spacing: 0.5px;
    text-transform: uppercase; line-height: 36px; text-shadow: 0 1px 3px var(--text-shadow);
  }
  .contact-phone {
    position: absolute; right: 82px; top: 47px; display: flex; align-items: center; gap: 5px;
    font-size: 21px; line-height: 28px; text-shadow: 0 1px 3px var(--text-shadow);
  }
  .contact-phone svg { width: 20px; height: 20px; }

  .hero-content { position: absolute; left: 0; right: 0; top: 236px; text-align: center; }
  .hero-title {
    font-family: "Oswald", sans-serif; font-weight: 400; font-size: 56px; line-height: 76px;
    text-transform: uppercase; text-shadow: 0 3px 6px var(--text-shadow);
  }
  .hero-text {
    width: 640px; margin: 0 auto; font-size: 20px; line-height: 31px;
    text-shadow: 0 1px 4px var(--text-shadow);
  }
  .cta-button {
    display: inline-block; margin-top: 22px; width: 284px; height: 53px; line-height: 50px;
    border: 1.5px solid var(--accent); border-radius: 27px;
    background: radial-gradient(ellipse at center, var(--button-fill) 0%, var(--button-edge) 100%);
    box-shadow: 0 0 14px rgba(58, 216, 174, 0.45);
    font-family: "Roboto", sans-serif; font-weight: 500; font-size: 20px; color: var(--white); text-decoration: none;
  }

  .slide-nav { position: absolute; left: 1144px; top: 282px; width: 34px; height: 84px; }

  .site-footer {
    position: absolute; left: 0; bottom: 0; width: 100%; height: 96px;
    background: var(--footer-bg); border-top: 1px solid var(--footer-line);
  }
  .copyright { position: absolute; left: 104px; top: 40px; font-size: 18px; line-height: 24px; }
  .social-links { position: absolute; left: 904px; top: 37px; display: flex; gap: 7px; }
  .social-links span {
    width: 27px; height: 27px; border: 1.5px solid var(--white); border-radius: 50%;
    display: flex; align-items: center; justify-content: center;
  }
</style>
</head>
<body>
  <div class="hero-photo" role="img" aria-label="Dusk photograph of modern glass apartment buildings under a soft cloudy sky"></div>
  <div class="hero-shade"></div>

  <header class="site-header">
    <div class="menu-toggle" aria-label="Menu"><span></span><span></span><span></span></div>
    <div class="brand-name">Fresh Dwelling Tract Guide</div>
    <div class="contact-phone">
      <svg viewBox="0 0 20 20" aria-hidden="true">
        <rect x="0" y="0" width="20" height="20" rx="3" fill="#fff"/>
        <path d="M6 4.5 L8 4.2 L9 7.2 L7.7 8.3 C8.4 10 9.9 11.6 11.7 12.3 L12.8 11 L15.8 12 L15.5 14 C15.3 15 14.5 15.6 13.5 15.5 C8.6 15 5 11.4 4.5 6.5 C4.4 5.5 5 4.7 6 4.5 Z" fill="var(--phone-glyph)"/>
      </svg>
      <span>: 555 308 4172</span>
    </div>
  </header>

  <main class="hero-content">
    <h1 class="hero-title">Search for New Homes</h1>
    <p class="hero-text">Your own buyer's agent is usually paid by the builder, and works for you on price, upgrades and the contract</p>
    <a class="cta-button" href="#">Search For New Homes</a>
  </main>

  <nav class="slide-nav" aria-label="Slides">
    <svg width="34" height="84" viewBox="0 0 34 84">
      <line x1="8" y1="6" x2="25" y2="23" stroke="#fff" stroke-width="1.2"/>
      <circle cx="8" cy="6" r="4.5" fill="var(--accent)"/>
      <circle cx="25" cy="23" r="4.5" fill="#fff"/>
      <circle cx="25" cy="41" r="4.5" fill="#fff"/>
      <circle cx="25" cy="59" r="4.5" fill="#fff"/>
      <circle cx="25" cy="76" r="4.5" fill="#fff"/>
    </svg>
  </nav>

  <footer class="site-footer">
    <p class="copyright">Copyright © 2018. All Rights Reserved</p>
    <div class="social-links">
      <span></span><span></span><span></span><span></span><span></span>
      <span>
        <svg width="13" height="10" viewBox="0 0 13 10" aria-label="Email">
          <rect x="0.7" y="0.7" width="11.6" height="8.6" rx="1" fill="none" stroke="#fff" stroke-width="1.2"/>
          <path d="M1 1.5 L6.5 5.5 L12 1.5" fill="none" stroke="#fff" stroke-width="1.2"/>
        </svg>
      </span>
    </div>
  </footer>
</body>
</html>
```